Company web site

Looking for a full responsive(mobile friendly) wordpress implementation

Some material is in the website -- brelvanto.wordpress.com

But looking for a template more consistent with the logo design, and more future looking.

Target Market(s)

Enterprise Clients

Industry/Entity Type

It Company

Font styles to use
Sans Serif

Colors
33a6d7
0255a3
0455a3
cfdeed
85abd2
3176b5

Requirements
Must have
• about, contact information, partner page, success stories, customer testimonials. links to social presence.
• pricing information

```html
<!DOCTYPE html>
<html lang="en">
<head>
<meta charset="utf-8">
<title>Brelvanto – Blog</title>
<link href="https://fonts.googleapis.com/css2?family=Open+Sans:wght@400;600;700&family=Exo+2:wght@500;600;700&display=swap" rel="stylesheet">
<style>
:root{
  --blue:#33a6d7;
  --blue-deep:#0255a3;
  --blue-mid:#3176b5;
  --blue-soft:#cfdeed;
  --blue-pale:#c4e3f3;
  --ink:#222;
  --text:#555;
  --muted:#888;
  --line:#e3e3e3;
  --topbar:#5a5a5a;
  --crumb:#e1e1e1;
  --footer:#1c2633;
  --white:#fff;
}
*{box-sizing:border-box;margin:0;padding:0}
html,body{width:1200px;height:3035px;overflow:hidden}
body{position:relative;background:var(--white);font-family:"Open Sans",Arial,sans-serif;color:var(--text)}
.abs{position:absolute}

/* top bar */
.topbar{left:0;top:0;width:1200px;height:30px;background:var(--topbar);color:#eee;font-size:12px}
.topbar .call{position:absolute;left:81px;top:7px;display:flex;align-items:center;gap:8px;white-space:nowrap}
.topbar .social{position:absolute;right:81px;top:0;height:30px;display:flex}
.topbar .social span{width:38px;height:30px;border-left:1px solid #777;display:flex;align-items:center;justify-content:center}
.topbar .social span:last-child{border-right:1px solid #777}
.dot{width:10px;height:10px;border-radius:50%;background:#eee;display:block}

/* header */
.header{left:0;top:30px;width:1200px;height:98px;background:var(--white)}
.brand{position:absolute;left:81px;top:34px;display:flex;align-items:center;gap:10px;font-weight:700;font-size:26px;color:var(--blue)}
.brand .mark{width:24px;height:24px;border-radius:50%;background:var(--blue)}
.nav{position:absolute;left:0;top:0;height:98px;width:1200px}
.nav a{position:absolute;top:44px;font-family:"Exo 2",sans-serif;font-size:16px;color:#555;text-decoration:none;white-space:nowrap}
.nav a.active{top:0;height:98px;width:78px;background:var(--blue);color:#fff;display:flex;flex-direction:column;align-items:center;justify-content:center;gap:4px;font-weight:600}

/* hero */
.hero{left:0;top:128px;width:1200px;height:337px;background:linear-gradient(90deg,#050709 0%,#0c1118 45%,#1b2e48 70%,#3a6d9c 85%,#1a2c44 100%)}
.hero .visual{position:absolute;right:0;top:0;width:560px;height:337px;background:radial-gradient(circle at 60% 40%,#a9d3f0 0%,#4f8fc4 25%,#1c3656 60%,rgba(10,16,24,0) 85%)}
.hero h1{position:absolute;left:79px;top:140px;font-family:"Exo 2",sans-serif;font-weight:600;font-size:34px;line-height:42px;color:#fff;white-space:nowrap}
.hero h1 em{font-style:normal;color:var(--blue)}

.crumb{left:0;top:465px;width:1200px;height:37px;background:var(--crumb);font-size:13px;font-weight:700;padding:11px 0 0 79px;color:#444}
.crumb b{color:var(--blue)}
.crumb i{font-style:normal;color:var(--blue);margin:0 8px}

.section-title{left:0;top:565px;width:1200px;text-align:center;font-family:"Exo 2",sans-serif;font-weight:700;font-size:36px;color:var(--blue)}
.divider{left:324px;top:622px;width:552px;height:14px}

/* posts */
.post{left:81px;width:682px;height:628px;border:1px solid var(--line);background:#fff}
.post-head{height:95px;display:flex}
.post-date{width:60px;border-right:1px solid var(--line);padding:10px 0 0 16px;color:#333;font-size:11px;line-height:15px}
.post-date strong{display:block;font-size:28px;line-height:34px;font-weight:700;color:#111}
.post-meta{padding:16px 0 0 18px}
.post-title{font-size:22px;font-weight:700;color:var(--ink);white-space:nowrap}
.post-author{margin-top:8px;font-size:13px;font-weight:600;color:var(--blue)}
.post-author::before{content:"";display:inline-block;width:8px;height:8px;border-radius:50%;background:#999;margin-right:6px}
.post-image{height:322px}
.post-body{padding:22px 18px 0 18px;font-size:13.5px;line-height:26px;color:#555}
.post-actions{position:absolute;left:16px;bottom:14px;display:flex;align-items:center;gap:16px;font-size:12px;color:#666;white-space:nowrap}
.btn{width:150px;height:33px;border:2px solid #aaa;border-radius:5px;display:flex;align-items:center;justify-content:center;font-size:14px;font-weight:600;color:#555}
.btn.caps{font-weight:400;letter-spacing:.3px}
.act{display:flex;align-items:center;gap:6px;margin-left:10px}

/* sidebar */
.widget{left:793px;width:326px;border:1px solid var(--line);background:#fff}
.widget h4{font-size:15px;font-weight:400;color:#333;padding:18px 20px 0}
.search{margin:10px 20px 0;height:34px;background:#eee;font-size:12px;color:#888;display:flex;align-items:center;gap:6px;padding-left:10px}
.cat-list{list-style:none;margin-top:10px}
.cat-list li{height:37px;margin:0 20px;border-bottom:1px solid #eee;display:flex;align-items:center;font-size:13px;color:#555;padding-left:20px;position:relative}
.cat-list li::before{content:"";position:absolute;left:6px;top:14px;border:4px solid transparent;border-left:5px solid var(--blue)}
.cat-list li span{margin-left:auto;padding-right:6px;color:#777}
.cat-list li.on{background:var(--blue-pale)}
.cat-list li:last-child{border-bottom:0}
.tabs{display:flex;margin:16px 20px 0;border-bottom:1px solid #ddd;font-size:14px;line-height:18px;color:#333;white-space:nowrap}
.tabs span{display:block;padding:0 0 9px;flex:none}
.tabs span.sep{width:1px;height:16px;padding:0;margin:1px 18px 0;background:#ddd}
.tabs span.on{border-bottom:2px solid var(--blue);margin-bottom:-1px}
.tabs span.last{margin-left:auto}
.recent{margin:16px 20px 0;display:flex;gap:12px;height:56px}
.recent + .recent{margin-top:16px}
.recent .thumb{width:52px;height:52px;flex:none;background:linear-gradient(135deg,#0f2440,#4e8cc4 55%,#1a3a5e)}
.recent p{font-size:12.5px;line-height:17px;color:#333}
.recent small{display:block;margin-top:4px;font-size:11px;color:#999}

/* footer */
.footer{left:0;top:2688px;width:1200px;height:303px;background:var(--footer);color:#ddd}
.footer h5{position:absolute;top:48px;font-family:"Exo 2",sans-serif;font-size:20px;font-weight:600;color:#fff;white-space:nowrap}
.footer h5 em{font-style:normal;color:var(--blue)}
.footer h5::after{content:"";position:absolute;left:0;top:34px;width:170px;height:1px;background:#445}
.qlinks{position:absolute;left:81px;top:110px;list-style:none;font-size:15px;line-height:28px}
.qlinks li::before{content:"•";color:var(--blue);margin-right:10px}
.qlinks li.on{color:var(--blue);font-weight:600}
.contact{position:absolute;left:290px;top:110px;font-size:14.5px;line-height:22px;white-space:nowrap}
.contact b{color:#fff}
.contact .row{display:flex;align-items:center;gap:10px;margin-top:12px}
.map{left:587px;top:113px;width:240px;height:154px;background:linear-gradient(135deg,#d9dde1,#c6ccd2 60%,#e4e6e8)}
.foot-brand{left:887px;top:110px;width:190px;text-align:center}
.foot-brand .mark{width:48px;height:48px;border-radius:50%;background:var(--blue);margin:0 auto 10px}
.foot-brand .name{font-size:32px;font-weight:700;color:var(--blue)}
.foot-brand .soc{display:flex;justify-content:center;gap:22px;margin-top:14px}
.copyright{left:0;top:2991px;width:1200px;height:44px;background:var(--blue-mid);color:#fff;font-size:13px;text-align:center;line-height:44px}
</style>
</head>
<body>

<div class="abs topbar">
  <div class="call">
    <svg width="12" height="12" viewBox="0 0 24 24"><path fill="#eee" d="M6.6 10.8c1.4 2.8 3.8 5.1 6.6 6.6l2.2-2.2c.3-.3.7-.4 1-.2 1.1.4 2.3.6 3.6.6.6 0 1 .4 1 1V20c0 .6-.4 1-1 1C10.6 21 3 13.4 3 4c0-.6.4-1 1-1h3.5c.6 0 1 .4 1 1 0 1.3.2 2.5.6 3.6.1.3 0 .7-.2 1z"/></svg>
    <span>Call Us : <b>+123 456 7890</b></span>
  </div>
  <div class="social"><span><i class="dot"></i></span><span><i class="dot"></i></span><span><i class="dot"></i></span><span><i class="dot"></i></span></div>
</div>

<header class="abs header">
  <div class="brand"><span class="mark"></span>Brelvanto</div>
  <nav class="nav">
    <a style="left:560px">Home</a>
    <a style="left:644px">Platform</a>
    <a style="left:751px">Partners</a>
    <a class="active" style="left:858px">
      <svg width="24" height="20" viewBox="0 0 24 20"><path fill="#fff" d="M2 1h20v13H9l-5 4v-4H2z"/><circle cx="8" cy="7.5" r="1.3" fill="#33a6d7"/><circle cx="12" cy="7.5" r="1.3" fill="#33a6d7"/><circle cx="16" cy="7.5" r="1.3" fill="#33a6d7"/></svg>
      Blog
    </a>
    <a style="left:973px">About</a>
    <a style="left:1058px">Contact</a>
  </nav>
</header>

<section class="abs hero">
  <div class="visual" role="img" aria-label="Photo of a hand holding a tablet with a glowing globe and floating screens above it"></div>
  <h1>Bridging <em>Connected Devices</em><br>With <em>Enterprise Solutions</em></h1>
</section>

<div class="abs crumb">HOME<i>»</i><b>BLOG</b></div>

<h2 class="abs section-title">BLOG</h2>
<svg class="abs divider" viewBox="0 0 552 14"><line x1="0" y1="7" x2="250" y2="7" stroke="#ccc"/><line x1="302" y1="7" x2="552" y2="7" stroke="#ccc"/><circle cx="276" cy="7" r="6" fill="none" stroke="#bbb" stroke-width="2"/></svg>

<article class="abs post" style="top:672px">
  <div class="post-head">
    <div class="post-date"><strong>03</strong>JUL<br>2017</div>
    <div class="post-meta"><div class="post-title">Lorem Ipsum is not simply random text.</div><div class="post-author">Admin</div></div>
  </div>
  <div class="post-image" role="img" aria-label="Photo of a businessman touching a cluster of glowing gears" style="background:linear-gradient(120deg,#0d3a5c,#1f6d9e 45%,#7fb8d8 70%,#2a6f99)"></div>
  <p class="post-body">Lorem Ipsum is simply dummy text of the printing and typesetting industry. Lorem Ipsum has been the industry's standard dummy text ever since the 1500s, when an unknown printer took a galley of type and scrambled it to make a type specimen book. It has survived not only five centuries, but also the leap into electronic typesetting, remaining essentially unchanged. It was popularised in the 1960s with the release of Letraset sheets containing Lorem Ipsum passages.</p>
  <div class="post-actions"><span class="btn">Read More</span><span class="btn caps">LEAVE A REPLY</span><span class="act">◌ Comments : 0</span><span class="act">&lt; Share It</span></div>
</article>

<article class="abs post" style="top:1330px">
  <div class="post-head">
    <div class="post-date"><strong>03</strong>JUL<br>2017</div>
    <div class="post-meta"><div class="post-title">Lorem Ipsum is not simply random text.</div><div class="post-author">Admin</div></div>
  </div>
  <div class="post-image" role="img" aria-label="Photo of a hand reaching toward glowing device and message icons" style="background:linear-gradient(120deg,#3b7cc4,#1d4f93 40%,#6aa6e0 65%,#2a5ea8)"></div>
  <p class="post-body">Lorem Ipsum is simply dummy text of the printing and typesetting industry. Lorem Ipsum has been the industry's standard dummy text ever since the 1500s, when an unknown printer took a galley of type and scrambled it to make a type specimen book. It has survived not only five centuries, but also the leap into electronic typesetting, remaining essentially unchanged. It was popularised in the 1960s with the release of Letraset sheets containing Lorem Ipsum passages.</p>
  <div class="post-actions"><span class="btn">Read More</span><span class="btn caps">LEAVE A REPLY</span><span class="act">◌ Comments : 0</span><span class="act">&lt; Share It</span></div>
</article>

<article class="abs post" style="top:1988px">
  <div class="post-head">
    <div class="post-date"><strong>03</strong>JUL<br>2017</div>
    <div class="post-meta"><div class="post-title">Lorem Ipsum is not simply random text.</div><div class="post-author">Admin</div></div>
  </div>
  <div class="post-image" role="img" aria-label="Photo of a hand reaching toward a stream of floating picture screens" style="background:linear-gradient(100deg,#1c4d80,#5c92c4 35%,#cfe2f2 60%,#8fb8dc 85%,#4d7eb0)"></div>
  <p class="post-body">Lorem Ipsum is simply dummy text of the printing and typesetting industry. Lorem Ipsum has been the industry's standard dummy text ever since the 1500s, when an unknown printer took a galley of type and scrambled it to make a type specimen book. It has survived not only five centuries, but also the leap into electronic typesetting, remaining essentially unchanged. It was popularised in the 1960s with the release of Letraset sheets containing Lorem Ipsum passages.</p>
  <div class="post-actions"><span class="btn">Read More</span><span class="btn caps">LEAVE A REPLY</span><span class="act">◌ Comments : 0</span><span class="act">&lt; Share It</span></div>
</article>

<aside class="abs widget" style="top:672px;height:97px">
  <h4>Search</h4>
  <div class="search"><svg width="10" height="10" viewBox="0 0 10 10"><circle cx="4" cy="4" r="3" fill="none" stroke="#666" stroke-width="1.4"/><line x1="6.3" y1="6.3" x2="9" y2="9" stroke="#666" stroke-width="1.4"/></svg>Search Now !</div>
</aside>

<aside class="abs widget" style="top:795px;height:316px">
  <h4>Categories</h4>
  <ul class="cat-list">
    <li>Lorem Ipsum<span>(8)</span></li>
    <li>Lorem Ipsum<span>(28)</span></li>
    <li>Lorem Ipsum<span>(4)</span></li>
    <li class="on">Lorem Ipsum<span>(1)</span></li>
    <li>Lorem Ipsum<span>(2)</span></li>
    <li>Lorem Ipsum<span>(1)</span></li>
    <li>Lorem Ipsum<span>(1)</span></li>
  </ul>
</aside>

<aside class="abs widget" style="top:1137px;height:276px">
  <div class="tabs"><span class="on">Recent Posts</span><span class="sep"></span><span>Popular Posts</span><span class="sep last"></span><span>Tags</span></div>
  <div class="recent"><div class="thumb" role="img" aria-label="Post thumbnail photo"></div><div><p>Lorem Ipsum is not simply random text.</p><small>Jul 03, 2017</small></div></div>
  <div class="recent"><div class="thumb" role="img" aria-label="Post thumbnail photo"></div><div><p>Lorem Ipsum is not simply random text.</p><small>Jul 03, 2017</small></div></div>
  <div class="recent"><div class="thumb" role="img" aria-label="Post thumbnail photo"></div><div><p>Lorem Ipsum is not simply random text.</p><small>Jul 03, 2017</small></div></div>
</aside>

<footer class="abs footer">
  <h5 style="left:81px">Quick <em>Links</em></h5>
  <ul class="qlinks">
    <li class="on">Home</li><li>Platform</li><li>Partners</li><li>Blog</li><li>About</li><li>Contact</li>
  </ul>
  <h5 style="left:290px">Contact <em>Details</em></h5>
  <div class="contact">
    <b>Brelvanto</b><br>123, Lorem ipsum dolor sit amet,<br>euismod - 123 456
    <div class="row"><svg width="13" height="13" viewBox="0 0 24 24"><path fill="#33a6d7" d="M6.6 10.8c1.4 2.8 3.8 5.1 6.6 6.6l2.2-2.2c.3-.3.7-.4 1-.2 1.1.4 2.3.6 3.6.6.6 0 1 .4 1 1V20c0 .6-.4 1-1 1C10.6 21 3 13.4 3 4c0-.6.4-1 1-1h3.5c.6 0 1 .4 1 1 0 1.3.2 2.5.6 3.6.1.3 0 .7-.2 1z"/></svg>123 456 7890</div>
    <div class="row"><svg width="14" height="13" viewBox="0 0 14 13"><rect x="1" y="4" width="12" height="6" fill="#33a6d7"/><rect x="3" y="1" width="8" height="3" fill="none" stroke="#33a6d7"/><rect x="3" y="9" width="8" height="3" fill="#fff"/></svg>123 456 7890</div>
    <div class="row"><svg width="14" height="10" viewBox="0 0 14 10"><rect x="0.5" y="0.5" width="13" height="9" fill="#33a6d7"/><path d="M1 1l6 5 6-5" fill="none" stroke="#1c2633"/></svg>info@brelvanto.com</div>
  </div>
  <h5 style="left:587px">Location <em>Map</em></h5>
  <div class="abs map" role="img" aria-label="Street map showing the office location with a red pin"></div>
  <div class="abs foot-brand">
    <div class="mark"></div>
    <div class="name">Brelvanto</div>
    <div class="soc"><i class="dot"></i><i class="dot"></i><i class="dot"></i><i class="dot"></i></div>
  </div>
</footer>
<div class="abs copyright">Copyright © 2017 <b>Brelvanto</b>. All Right Reserved.</div>

</body>
</html>
```